Sickle Cell Patient Flyer

I need this be appealing to families dealing with sickle cell disease. Both informative-introducing the idea that a stroke prevention program is not only easy for their children but necessary. Stroke is a risk to all with children with SCD.
I included a few info flyers from the Vessel Alliance and licensed to me photos I like. I am open to suggestions.
web address is brightpathwellbeing.net
Call to schedule 833-412-7086
TCD is a safe and accurate tool that makes stroke prevention possible for your SCD patients and family.
Risk is highest for SCD sufferers age 2 to 5. Protect your childs future.

Target Market(s)

Parents, families and medical professionals

Industry/Entity Type

Medical wellness

Font styles to use
Other font styles liked:
• something close to my logo font

Colors
0094D4
00A9DD
6FCCEA
C7EBF8
E9F6FB

Requirements
Nice to have
• pictures of kids (Children of color) pictures of Brains, kids happy with medical professionals
Should not have
• dark colors

```html
<!DOCTYPE html>
<html lang="en">
<head>
<meta charset="utf-8">
<title>Stroke Prevention for Children with Sickle Cell Disease</title>
<link href="https://fonts.googleapis.com/css2?family=Arimo:wght@400;500;700&display=swap" rel="stylesheet">
<style>
  :root {
    --navy: #0f4c81;
    --blue: #11a8df;
    --blue-deep: #0094d4;
    --sky: #6fccea;
    --ice: #e9f6fb;
    --mint: #72c8a3;
    --ink: #111111;
    --grey: #666b70;
    --backdrop: #eef1f3;
    --paper: #ffffff;
    --red: #d3232f;
  }
  * { box-sizing: border-box; margin: 0; padding: 0; }
  html, body { width: 907px; height: 1200px; overflow: hidden; }
  body { background: var(--backdrop); font-family: "Arimo", Arial, sans-serif; position: relative; }

  .flyer { position: absolute; left: 43px; top: 25px; width: 820px; height: 1150px; background: var(--paper); overflow: hidden; box-shadow: 0 6px 18px rgba(0,0,0,.12); }
  .flyer > * { position: absolute; }

  .hero-blue { left: 425px; top: 0; width: 395px; height: 210px; background: var(--blue); }
  .hero-mint { left: 500px; top: 175px; width: 320px; height: 163px; background: var(--mint); }
  .brain-sketch { left: 477px; top: 29px; width: 298px; height: 80px; background: rgba(255,255,255,.25); border-radius: 40px; }
  .child-photo { left: 560px; top: 112px; width: 230px; height: 226px; background: linear-gradient(180deg, #6b4a3a 0%, #b07a5a 35%, #f2f2f2 60%, #e4e4e4 100%); }
  .cell-doodle { background: var(--ice); border-radius: 50%; }
  .cell-doodle.top { left: 440px; top: 35px; width: 80px; height: 70px; }
  .cell-doodle.left { left: 70px; top: 232px; width: 95px; height: 70px; }
  .cell-doodle.right { left: 630px; top: 425px; width: 150px; height: 160px; }
  .cell-doodle.low { left: 690px; top: 728px; width: 95px; height: 68px; }

  .brand-name { left: 40px; top: 90px; width: 360px; color: var(--navy); font-weight: 700; font-size: 50px; line-height: 54px; letter-spacing: -0.5px; }

  .headline { left: 50px; top: 325px; color: var(--navy); font-weight: 500; font-size: 37px; letter-spacing: -0.3px; }
  .audience-band { left: 0; top: 378px; width: 820px; height: 34px; background: var(--blue); }
  .audience-band::before { content: ""; position: absolute; left: 0; top: 0; width: 40px; height: 34px; background: var(--mint); }
  .audience-band span { position: absolute; left: 50px; top: 5px; color: #fff; font-weight: 500; font-size: 25px; letter-spacing: 3.6px; }
  .headline-accent { left: 50px; top: 420px; color: var(--blue); font-weight: 700; font-size: 49px; letter-spacing: -0.5px; }

  .facts { left: 0; top: 0; width: 820px; height: 0; list-style: none; }
  .fact { position: absolute; left: 52px; width: 740px; }
  .fact .icon { position: absolute; left: 0; top: 0; width: 59px; height: 59px; border: 1.5px solid var(--blue); border-radius: 10px; display: flex; align-items: center; justify-content: center; }
  .fact p { position: absolute; left: 94px; top: 6px; width: 640px; color: var(--ink); font-size: 19px; line-height: 26px; letter-spacing: -0.2px; }
  .fact .rule { position: absolute; left: 95px; height: 7px; }
  .fact.screening { top: 513px; }
  .fact.screening .rule { top: 46px; width: 416px; background: var(--mint); }
  .fact.ultrasound { top: 597px; }
  .fact.ultrasound .rule { top: 43px; width: 572px; background: var(--blue); }
  .fact.risk { top: 683px; }
  .fact.risk p { top: 4px; }
  .fact .highlight { color: var(--blue); font-weight: 500; }

  .summary { left: 49px; top: 784px; width: 470px; color: var(--grey); font-size: 19px; line-height: 26px; letter-spacing: -0.2px; }

  .partners { left: 52px; top: 915px; display: flex; align-items: center; gap: 26px; }
  .partner { display: flex; align-items: center; gap: 8px; color: var(--red); font-size: 16px; font-weight: 500; }
  .partner .mark { width: 52px; height: 52px; border-radius: 50%; border: 2px solid var(--red); }
  .partner .tagline { display: block; font-size: 20px; font-weight: 400; margin-top: 3px; }

  .brain-art { left: 467px; top: 818px; width: 353px; height: 332px; border-radius: 48% 40% 20% 30%; background: linear-gradient(135deg, #1a8fa8 0%, #2bb673 30%, #e8312f 55%, #f7a21b 75%, #7b2fa8 100%); }

  .cta-band { left: 0; top: 1004px; width: 820px; height: 72px; background: var(--blue); }
  .cta-label { left: 49px; top: 1021px; color: #fff; font-size: 16px; line-height: 21px; }
  .cta-divider { left: 154px; top: 1021px; width: 2px; height: 37px; background: #fff; }
  .cta-phone { left: 174px; top: 1017px; color: #fff; font-size: 40px; font-weight: 500; letter-spacing: -0.5px; }
  .web-band { left: 0; top: 1076px; width: 820px; height: 74px; background: var(--ice); }
  .web-address { left: 49px; top: 1092px; color: var(--blue-deep); font-size: 32px; font-weight: 500; letter-spacing: -0.4px; }
  .brain-art { z-index: 2; }
</style>
</head>
<body>
<main class="flyer">
  <div class="hero-blue"></div>
  <div class="hero-mint"></div>
  <div class="brain-sketch" role="img" aria-label="White line drawing of two brains"></div>
  <div class="child-photo" role="img" aria-label="Photo of a smiling boy in a white shirt and red tie pointing upward"></div>
  <div class="cell-doodle top" role="img" aria-label="Outlined sickle cell doodles"></div>
  <div class="cell-doodle left" role="img" aria-label="Outlined sickle cell doodles"></div>
  <div class="cell-doodle right" role="img" aria-label="Outlined sickle cell doodles"></div>
  <div class="cell-doodle low" role="img" aria-label="Outlined sickle cell doodles"></div>

  <h1 class="brand-name">Bright Path<br>Wellbeing</h1>

  <h2 class="headline">STROKE PREVENTION</h2>
  <div class="audience-band"><span>FOR CHILDREN WITH SICKLE CELL DISEASE</span></div>
  <h2 class="headline-accent">IS POSSIBLE!</h2>

  <ul class="facts">
    <li class="fact screening">
      <span class="icon">
        <svg width="42" height="42" viewBox="0 0 42 42" fill="none" stroke="#72c8a3" stroke-width="1.5">
          <rect x="4" y="5" width="34" height="24" rx="2"/>
          <path d="M21 10c-3 4-5 6.5-5 9a5 5 0 0 0 10 0c0-2.5-2-5-5-9z"/>
          <path d="M8 33h26M8 37h26"/>
        </svg>
      </span>
      <p>Simple and Painless Screening for your child.</p>
      <span class="rule"></span>
    </li>
    <li class="fact ultrasound">
      <span class="icon">
        <svg width="42" height="42" viewBox="0 0 42 42" fill="none" stroke="#72c8a3" stroke-width="1.5">
          <path d="M5 12a22 22 0 0 1 32 0M10 17a15 15 0 0 1 22 0M15 22a8 8 0 0 1 12 0"/>
          <path d="M16 30a5 5 0 0 1 10 0z"/>
          <path d="M21 30v9M18 34h3"/>
        </svg>
      </span>
      <p>Our Screening uses Ultrasound which is Transcranial Doppler.</p>
      <span class="rule"></span>
    </li>
    <li class="fact risk">
      <span class="icon">
        <svg width="42" height="42" viewBox="0 0 42 42" fill="none" stroke="#72c8a3" stroke-width="1.5" stroke-linejoin="round">
          <path d="M24 4l-9 17h7l-5 17 13-21h-7l5-13z"/>
        </svg>
      </span>
      <p>About 11% of SCD patients have strokes before age 20<br>with <span class="highlight">THE HIGHEST RISK BETWEEN AGE 2 AND 5.</span></p>
    </li>
  </ul>

  <p class="summary">Screening or early signs of stroke can be a tool to for early diagnosis allowing for treatments that eliminate the risk.</p>

  <div class="partners">
    <div class="partner"><span class="mark"></span></div>
    <div class="partner"><span>Vessel Alliance<span class="tagline">United for Healthy Minds</span></span></div>
  </div>

  <div class="brain-art" role="img" aria-label="Colourful illustration of a human brain"></div>

  <div class="cta-band"></div>
  <p class="cta-label">CALL TO<br>SCHEDULE</p>
  <div class="cta-divider"></div>
  <p class="cta-phone">833-412-7086</p>
  <div class="web-band"></div>
  <p class="web-address">brightpathwellbeing.net</p>
</main>
</body>
</html>
```